Disability provider requiring digital flyer to promote services

My company works within the Disability sector (KTAP registered provider), currently operating in Sydney, Australia.
I require a digital brochure which lists our services and gives potential customers a quick look into what we do with a single glance.
Undecided whether this digital flyer is to be single or double sided, happy to consult with an experienced designer in this regard.
I prefer minimalist designs (which may be an issue for someone trying to convey information, I'm not sure), and possibly someone who can work with out watercolor logo.
Services include:
-Supported Independent Living
-Specialist Disability Accommodation
-Individualised Living Options Stage 1 & 2
-Home Modifications
-Occupational Therapy
-Support Coordination Levels 1 & 2
-Short Term Accommodation - STA Respite
-Drop In Supports
-Community Access
Disability

```html
<!DOCTYPE html>
<html lang="en">
<head>
<meta charset="utf-8">
<title>Clearview Healthcare – Services Flyer</title>
<link href="https://fonts.googleapis.com/css2?family=Bebas+Neue&family=Great+Vibes&family=Poppins:wght@400;500;600;700&display=swap" rel="stylesheet">
<style>
  :root {
    --green: #27b06d;
    --green-dark: #1f9a5c;
    --orange: #f68b3c;
    --teal: #2dbf98;
    --ink: #1c1c1c;
    --text: #2a2a2a;
    --paper: #ffffff;
    --paper-soft: #f4f4f4;
    --backdrop: #ececec;
  }
  * { box-sizing: border-box; margin: 0; padding: 0; }
  html, body { width: 1200px; height: 2426px; overflow: hidden; }
  body { background: var(--backdrop); font-family: "Poppins", Arial, sans-serif; color: var(--text); }

  .flyer {
    position: absolute; left: 40px; top: 420px;
    width: 1120px; height: 1585px;
    background: var(--paper-soft); overflow: hidden;
    box-shadow: 0 18px 40px rgba(0,0,0,0.18);
  }
  .shapes { position: absolute; inset: 0; }

  .photo {
    position: absolute;
  }
  .photo--carer {
    left: 560px; top: 215px; width: 540px; height: 620px;
    background: radial-gradient(ellipse at 50% 45%, #e9eef2 0%, #c9d3db 45%, rgba(200,210,218,0) 72%);
  }
  .photo--family {
    left: 0; top: 985px; width: 540px; height: 472px;
    background: linear-gradient(180deg, #f3f3f1 0%, #d8dcd6 45%, #9fb2c8 100%);
  }

  .brand-mark {
    position: absolute; left: 790px; top: 120px; width: 240px;
    display: flex; flex-direction: column; align-items: center; gap: 12px;
  }
  .brand-mark__dot { width: 60px; height: 60px; border-radius: 50%; background: var(--orange); }
  .brand-mark__name { font-weight: 600; font-size: 26px; color: var(--green-dark); text-align: center; line-height: 1.2; }

  .headline {
    position: absolute; left: 52px; top: 130px;
    font-family: "Bebas Neue", Impact, sans-serif;
    font-size: 178px; line-height: 1; color: var(--ink); letter-spacing: 1px;
  }
  .headline-script {
    position: absolute; left: 40px; top: 255px;
    font-family: "Great Vibes", cursive;
    font-size: 170px; line-height: 1; color: #ffffff;
  }
  .tagline {
    position: absolute; left: 46px; top: 459px; width: 690px; height: 70px;
    background: var(--orange); border-radius: 35px;
    display: flex; align-items: center; padding-left: 32px;
    font-weight: 600; font-size: 33px; color: var(--ink);
  }

  .welcome { position: absolute; left: 55px; top: 720px; width: 450px; }
  .welcome__kicker { font-weight: 500; font-size: 40px; color: var(--orange); line-height: 1.1; }
  .welcome__name { font-weight: 500; font-size: 33px; color: var(--ink); margin-top: 6px; }
  .welcome__text { font-size: 17.5px; line-height: 24px; margin-top: 10px; color: var(--text); }

  .services { position: absolute; left: 552px; top: 872px; width: 540px; }
  .services__title { font-weight: 600; font-size: 42px; letter-spacing: 1px; color: var(--ink); }
  .services__title span { color: var(--orange); }
  .services__list {
    list-style: none; position: relative; height: 500px;
  }
  .service {
    position: absolute; display: flex; align-items: center; gap: 26px;
    font-weight: 600; font-size: 16px; line-height: 21px; color: var(--ink);
  }
  .service svg { width: 52px; height: 52px; flex: none; fill: var(--orange); }
  .service span { width: 180px; }

  .contact-bar { position: absolute; left: 0; top: 1457px; width: 1120px; height: 128px; }
  .phone {
    position: absolute; left: 52px; top: 1490px;
    display: flex; align-items: center; gap: 32px;
    font-weight: 600; font-size: 54px; color: #fff; letter-spacing: -1px;
  }
  .phone svg { width: 44px; height: 44px; }
  .web { position: absolute; left: 648px; top: 1482px; color: #fff; font-size: 22px; line-height: 38px; }
  .web p { display: flex; align-items: center; gap: 10px; }
  .web svg { width: 20px; height: 20px; fill: #fff; }
</style>
</head>
<body>
<main class="flyer">
  <svg class="shapes" viewBox="0 0 1120 1585" aria-hidden="true">
    <rect x="0" y="0" width="1120" height="650" fill="var(--green)"/>
    <path d="M0 640 C120 610 230 655 360 630 C460 612 520 640 560 628 L1120 628 L1120 1585 L0 1585 Z" fill="var(--paper)"/>
    <rect x="540" y="628" width="580" height="830" fill="var(--paper-soft)"/>
    <circle cx="985" cy="95" r="320" fill="var(--paper-soft)"/>
    <path d="M665 0 C690 190 860 320 1120 300" fill="none" stroke="var(--green-dark)" stroke-width="3" opacity="0.5"/>
  </svg>

  <div class="photo photo--carer" role="img" aria-label="Photo of a carer embracing a smiling older woman seated in a wheelchair"></div>

  <div class="brand-mark">
    <div class="brand-mark__dot"></div>
    <div class="brand-mark__name">Clearview Healthcare</div>
  </div>

  <h1 class="headline">CLEARVIEW</h1>
  <div class="headline-script">Healthcare</div>
  <div class="tagline">Clearview for an empowered future</div>

  <section class="welcome">
    <h2 class="welcome__kicker">WELCOME TO</h2>
    <h3 class="welcome__name">Clearview Healthcare</h3>
    <p class="welcome__text">Clearview Healthcare is a Sydney based disability support services provider. Focusing on intellectual, physical &amp; sensory disabilities including mental health within the Greater Sydney region, we strive to assist our participants in leading an independent and fulfilling life.</p>
  </section>

  <div class="photo photo--family" role="img" aria-label="Photo of a smiling young couple standing behind an older woman in a wheelchair"></div>

  <section class="services">
    <h2 class="services__title">SERVICES <span>INCLUDE:</span></h2>
    <ul class="services__list">
      <li class="service" style="left:0;top:58px">
        <svg viewBox="0 0 52 52"><circle cx="20" cy="8" r="6"/><path d="M12 16h16l4 16h-5v18h-6V36h-2v14h-6V32H4z"/><circle cx="40" cy="20" r="4"/><path d="M35 26h10l2 12h-3v12h-8V38h-3z"/></svg>
        <span>Supported Independent Living</span>
      </li>
      <li class="service" style="left:286px;top:58px">
        <svg viewBox="0 0 52 52"><path d="M26 4L2 26h7v22h13V34h8v14h13V26h7z"/></svg>
        <span>Home Modifications</span>
      </li>
      <li class="service" style="left:0;top:166px">
        <svg viewBox="0 0 52 52"><circle cx="14" cy="7" r="5"/><path d="M8 14h12l3 16h-4v18h-5V34h-2v14H7V30H4z"/><circle cx="36" cy="38" r="11" fill="none" stroke="#f68b3c" stroke-width="4"/><circle cx="36" cy="16" r="4"/><path d="M32 22h8v10h-8z"/></svg>
        <span>Specialist Disability Accommodation</span>
      </li>
      <li class="service" style="left:286px;top:166px">
        <svg viewBox="0 0 52 52"><rect x="4" y="6" width="26" height="14"/><rect x="34" y="6" width="14" height="8"/><rect x="8" y="26" width="36" height="8"/><rect x="8" y="34" width="6" height="14"/><rect x="38" y="34" width="6" height="14"/></svg>
        <span>Individualised Living Options Stage 1 &amp; 2</span>
      </li>
      <li class="service" style="left:0;top:278px">
        <svg viewBox="0 0 52 52"><path d="M22 4L2 22h6v24h28V22h6z"/><circle cx="40" cy="40" r="10" fill="none" stroke="#f68b3c" stroke-width="4"/></svg>
        <span>Short Term Accommodation - STA Respite</span>
      </li>
      <li class="service" style="left:286px;top:278px">
        <svg viewBox="0 0 52 52"><circle cx="26" cy="7" r="6"/><path d="M18 15h16v12H18z"/><circle cx="10" cy="32" r="5"/><circle cx="42" cy="32" r="5"/><path d="M3 40h14v10H3zM35 40h14v10H35zM22 34h8v16h-8z"/></svg>
        <span>Support Coordination Levels 1 &amp; 2</span>
      </li>
      <li class="service" style="left:0;top:378px">
        <svg viewBox="0 0 52 52"><rect x="6" y="4" width="8" height="8"/><rect x="4" y="14" width="12" height="34"/><rect x="24" y="4" width="10" height="10"/><rect x="20" y="18" width="18" height="6"/><rect x="22" y="24" width="4" height="24"/><rect x="32" y="24" width="4" height="24"/><rect x="40" y="10" width="8" height="38"/></svg>
        <span>Occupational Therapy</span>
      </li>
      <li class="service" style="left:286px;top:378px">
        <svg viewBox="0 0 52 52"><circle cx="16" cy="12" r="7"/><circle cx="36" cy="12" r="7"/><circle cx="26" cy="26" r="7"/><path d="M2 34c0-8 8-12 14-12 2 0 4 1 4 1-4 3-6 7-6 11zM50 34c0-8-8-12-14-12-2 0-4 1-4 1 4 3 6 7 6 11zM12 48c0-8 6-13 14-13s14 5 14 13z"/></svg>
        <span>Community Access</span>
      </li>
      <li class="service" style="left:0;top:466px">
        <svg viewBox="0 0 52 52"><circle cx="28" cy="8" r="6"/><path d="M22 16h12v14H22z"/><path d="M2 34h10l12 6h14c3 0 3 4 0 4H24v2h16l10-10c2-2 4 0 2 2L40 50H12l-10-4z"/></svg>
        <span>Drop In Supports</span>
      </li>
    </ul>
  </section>

  <svg class="contact-bar" viewBox="0 0 1120 128" aria-hidden="true">
    <rect x="0" y="0" width="1120" height="128" fill="var(--teal)"/>
    <path d="M0 0 H520 C560 0 575 20 575 60 V128 H0 Z" fill="var(--orange)"/>
    <path d="M520 0 C565 0 580 22 580 60 V128 H592 V60 C592 22 575 0 530 0 Z" fill="var(--paper)"/>
  </svg>

  <div class="phone">
    <svg viewBox="0 0 44 44"><circle cx="22" cy="22" r="21" fill="#fff"/><path d="M15 11c1-1 3-1 4 1l2 4c1 2 0 3-1 4l-1 1c1 3 4 6 7 7l1-1c1-1 2-2 4-1l4 2c2 1 2 3 1 4l-2 2c-3 3-10 0-16-6S10 16 13 13z" fill="#f68b3c"/></svg>
    <span>61 0400 318 562</span>
  </div>

  <div class="web">
    <p><svg viewBox="0 0 20 20"><path d="M1 4h18v12H1z"/><path d="M1 4l9 7 9-7" fill="none" stroke="#2dbf98" stroke-width="1.6"/></svg>hello@clearviewcare.com.au</p>
    <p><svg viewBox="0 0 20 20"><circle cx="10" cy="10" r="9"/><path d="M1 10h18M10 1c-5 5-5 13 0 18M10 1c5 5 5 13 0 18" fill="none" stroke="#2dbf98" stroke-width="1.4"/></svg>www.clearviewcare.com.au</p>
  </div>
</main>
</body>
</html>
```